VENTURE CAPITAL GROUP BUSINESS CARD DESIGN

Venture Capital Group based in SF looking for a bold business card design. No trendy colour explosion, 3D effects etc. Just "simple" optical effects. Works on your brain, keeps your eye focused and sticks to your mind.
Target Market(s)
Technology startups
Industry/Entity Type
Venture Capital
Contact Information for Business Card
DESMOND WHITLAKE
MANAGING PARTNER
187 FENWORTH ST SAN FRANCISCO, CA 94187
415.555.0142 O
415.555.0147 F
415.555.0193 C
desmond@veldtmoorcapital.ventures

```html
<!DOCTYPE html>
<html lang="en">
<head>
<meta charset="utf-8">
<title>Veldtmoor Capital Group – Business Card</title>
<link rel="stylesheet" href="https://fonts.googleapis.com/css2?family=Cinzel:wght@500&family=EB+Garamond:wght@400;500&family=Libre+Baskerville:wght@700&display=swap">
<style>
  :root {
    --backdrop: #1b1b1b;
    --card-dark: #1f2120;
    --card-mid: #2c2e2d;
    --front-dark: #1d2620;
    --front-mid: #2a342d;
    --green: #1f8a3a;
    --green-bright: #2fb04c;
    --text-light: #d9d9d9;
    --text-muted: #bfbfbf;
    --divider: #8a8a8a;
  }
  html, body {
    margin: 0;
    width: 1200px;
    height: 873px;
    overflow: hidden;
    background: var(--backdrop);
  }
  .canvas {
    position: relative;
    width: 1200px;
    height: 873px;
  }
  .card {
    position: absolute;
    width: 540px;
    height: 309px;
    top: 282px;
    box-shadow: 0 14px 40px rgba(0,0,0,0.6);
    overflow: hidden;
  }
  .card-front {
    left: 40px;
    background: radial-gradient(ellipse at 45% 40%, var(--front-mid), var(--front-dark) 75%);
  }
  .card-back {
    left: 620px;
    background: radial-gradient(ellipse at 40% 45%, var(--card-mid), var(--card-dark) 75%);
  }
  .texture {
    position: absolute;
    inset: 0;
    background: linear-gradient(135deg, rgba(255,255,255,0.03), rgba(0,0,0,0.08));
  }
  .brand {
    position: absolute;
    display: flex;
    align-items: center;
    gap: 12px;
  }
  .brand-dot {
    width: 22px;
    height: 22px;
    border-radius: 50%;
    background: var(--green);
    flex: none;
  }
  .brand-name {
    font-family: "Cinzel", serif;
    font-weight: 500;
    color: var(--green);
    letter-spacing: 1px;
    line-height: 1.15;
    white-space: nowrap;
  }
  .card-front .brand {
    left: 0; right: 0; top: 132px;
    justify-content: center;
  }
  .card-front .brand-name { font-size: 27px; }
  .card-back .brand {
    left: 30px; top: 136px;
  }
  .card-back .brand-dot { width: 16px; height: 16px; }
  .card-back .brand-name { font-size: 15px; }
  .divider {
    position: absolute;
    left: 242px;
    top: 70px;
    width: 1px;
    height: 160px;
    background: linear-gradient(to bottom, transparent, var(--divider), transparent);
  }
  .person {
    position: absolute;
    left: 170px;
    top: 30px;
  }
  .person-name {
    font-family: "Libre Baskerville", serif;
    font-weight: 700;
    font-size: 19px;
    color: var(--green);
    margin: 0;
  }
  .person-title {
    font-family: "EB Garamond", serif;
    font-size: 13px;
    color: var(--text-light);
    margin: 2px 0 0 64px;
  }
  .contacts {
    position: absolute;
    left: 262px;
    top: 98px;
    margin: 0;
    padding: 0;
    list-style: none;
    font-family: "EB Garamond", serif;
    font-size: 14px;
    color: var(--text-muted);
  }
  .contacts li {
    display: flex;
    align-items: center;
    gap: 8px;
    height: 22px;
  }
  .contacts li.gap-before { margin-top: 6px; }
  .icon {
    width: 16px;
    height: 16px;
    flex: none;
  }
  .website {
    position: absolute;
    left: 0; right: 0;
    bottom: 30px;
    text-align: center;
    font-family: "EB Garamond", serif;
    font-size: 15px;
    letter-spacing: 2.5px;
    color: var(--text-muted);
  }
</style>
</head>
<body>
<main class="canvas">

  <section class="card card-front" aria-label="Card front">
    <div class="texture"></div>
    <div class="brand">
      <span class="brand-dot"></span>
      <span class="brand-name">Veldtmoor Capital Group</span>
    </div>
  </section>

  <section class="card card-back" aria-label="Card back">
    <div class="texture"></div>

    <div class="person">
      <h1 class="person-name">Desmond Whitlake</h1>
      <p class="person-title">Managing Partner</p>
    </div>

    <div class="brand">
      <span class="brand-dot"></span>
      <span class="brand-name">Veldtmoor<br>Capital Group</span>
    </div>

    <div class="divider"></div>

    <ul class="contacts">
      <li>
        <svg class="icon" viewBox="0 0 16 16"><circle cx="8" cy="8" r="8" fill="var(--green)"/><rect x="4" y="6" width="8" height="5" rx="1" fill="#fff"/><rect x="3.5" y="4.5" width="9" height="2" rx="1" fill="#fff"/></svg>
        415.555.0142
      </li>
      <li>
        <svg class="icon" viewBox="0 0 16 16"><circle cx="8" cy="8" r="8" fill="var(--green)"/><rect x="5" y="3.5" width="6" height="3" fill="#fff"/><rect x="3.5" y="6.5" width="9" height="4.5" rx="1" fill="#fff"/><rect x="5" y="10" width="6" height="2.5" fill="#fff"/></svg>
        415.555.0147
      </li>
      <li>
        <svg class="icon" viewBox="0 0 16 16"><circle cx="8" cy="8" r="8" fill="var(--green)"/><path d="M5 4l2 0.5 0.5 2-1.2 1a6 6 0 0 0 2.2 2.2l1-1.2 2 0.5 0.5 2c-4 0.8-8-3.2-7-7z" fill="#fff"/></svg>
        415.555.0193
      </li>
      <li class="gap-before">
        <svg class="icon" viewBox="0 0 16 16"><circle cx="8" cy="8" r="8" fill="var(--green)"/><rect x="4" y="5" width="8" height="6" fill="#fff"/><path d="M4 5l4 3.5L12 5" fill="none" stroke="var(--green)" stroke-width="1"/></svg>
        desmond@veldtmoorcapital.ventures
      </li>
      <li>
        <svg class="icon" viewBox="0 0 16 16"><circle cx="8" cy="8" r="8" fill="var(--green)"/><path d="M8 3.5a3 3 0 0 1 3 3c0 2.2-3 5.8-3 5.8s-3-3.6-3-5.8a3 3 0 0 1 3-3z" fill="#fff"/><circle cx="8" cy="6.5" r="1.1" fill="var(--green)"/></svg>
        187 Fenworth St San Francisco, CA 94187
      </li>
    </ul>

    <p class="website">www.veldtmoorcapital.ventures</p>
  </section>

</main>
</body>
</html>
```